Website for a Psychologist in Private Practice

I need a cool web design for my website: www.drkalvoric.com. I would like it to look professional. Keep all the current content and add: Space for video; radio spots (see Silver Cedar Tunes Logo below for those); Quick Inquiry; Friendora link; 5 star rating on Rivo; a map; reviews from former patients. I am open to suggestions.

Target Market(s)

Those seeking individual and marital counseling.

Industry/Entity Type

Mental Health

Number of Pages Required

1 page

Font styles to use
Sans Serif
Other font styles liked:
• I'm open but no hard to read script

Requirements
Must have
• All the content on my home page with link for video and radio spots. List services and degrees and expertices (pics not necessary).
Nice to have
• A video of me and radio conversations (logo of Silver Cedar Tunes radio attached).
Should not have
• Cartoons, comedy, etc.... I don't need pictures of services (marital, depression, etc...) Just list those.

```html
<!DOCTYPE html>
<html lang="en">
<head>
<meta charset="utf-8">
<title>Dr. Maren K. Kalvoric – Clinical Psychologist</title>
<link rel="stylesheet" href="https://fonts.googleapis.com/css2?family=Josefin+Sans:wght@300;400;600;700&family=Open+Sans:wght@400;600;700&family=Cormorant+Garamond:wght@400;500&display=swap">
<style>
:root{
  --gold:#c8ad4d;
  --gold-dark:#b2963a;
  --red:#e5262b;
  --navy:#1f5a8c;
  --blue:#3a86c8;
  --blue-soft:#7fa6d2;
  --ink:#333333;
  --muted:#6b6b6b;
  --paper:#ffffff;
  --page:#ebebe8;
  --field:#ececec;
  --star:#f0a21c;
}
*{box-sizing:border-box;margin:0;padding:0}
html,body{width:1200px;height:2667px;overflow:hidden;background:var(--page)}
body{font-family:"Open Sans",sans-serif;color:var(--ink)}
.page{position:relative;width:1200px;height:2667px;overflow:hidden;background:var(--page)}
.abs{position:absolute}

/* hero */
.hero-photo{left:0;top:0;width:1200px;height:720px;background:linear-gradient(180deg,#6f8ba8 0%,#9fb3c4 30%,#c9cfd0 46%,#5f87a2 52%,#3f6f8f 75%,#5a7d8e 100%)}
.beach-photo{left:0;top:720px;width:1200px;height:630px;background:linear-gradient(180deg,#5e8aa0 0%,#cfd6d2 22%,#e6ddcf 40%,#d9c6a8 70%,#cdb48e 100%)}
.hero-title{left:0;width:1200px;text-align:center;font-family:"Cormorant Garamond",serif;color:#fff;text-shadow:0 1px 3px rgba(0,0,0,.25)}
.hero-title.small{top:378px;font-size:36px}
.hero-title.large{top:408px;font-size:58px}
.slide-arrow{top:419px;width:36px;height:36px}

/* header */
.header{left:73px;top:71px;width:1052px;height:101px;background:var(--paper);border-bottom:5px solid var(--gold);box-shadow:0 2px 6px rgba(0,0,0,.15)}
.brand{position:absolute;left:22px;top:32px;font-family:"Josefin Sans",sans-serif;font-size:34px;font-weight:600;color:var(--gold)}
.brand .pre{font-weight:400}
.nav{position:absolute;left:380px;top:62px;display:flex;gap:20px;font-size:13px;font-weight:700;letter-spacing:.3px}
.social{position:absolute;left:640px;top:18px;display:flex;gap:8px;font-size:10px;color:var(--muted);font-weight:600}
.contact-tab{left:858px;top:0;width:257px;height:86px;background:var(--red);text-align:center;color:#fff;box-shadow:0 2px 4px rgba(0,0,0,.2)}
.contact-tab .phone{font-size:29px;font-weight:700;margin-top:8px}
.contact-tab .mail{font-size:13px;margin-top:-2px}
.address-ribbon{left:858px;top:86px;width:257px;height:76px}
.address-text{left:858px;top:98px;width:257px;text-align:center;color:#fff;font-size:13px;line-height:19px}

/* tiles */
.tile-panel{left:62px;top:711px;width:1076px;height:249px;background:rgba(255,255,255,.85)}
.tile{top:727px;width:345px;height:226px;overflow:hidden}
.tile-label{position:absolute;bottom:12px;font-family:"Josefin Sans",sans-serif;font-weight:600;font-size:24px;color:#fff}
.tile-portrait{left:75px;background:linear-gradient(160deg,#6c8e4c,#c6b08a 55%,#8a6f4e)}
.tile-video{left:427px;background:linear-gradient(160deg,#bfc5c4,#7e8b90 60%,#59656c)}
.tile-radio{left:780px;background:linear-gradient(180deg,#74c6c3,#5db6b4)}
.play-icon{position:absolute;left:137px;top:75px}
.radio-head{position:absolute;top:18px;width:100%;text-align:center;font-family:"Josefin Sans",sans-serif;font-weight:700;font-size:24px;color:#fff}
.radio-set{position:absolute;left:105px;top:58px;width:135px;height:85px;border-radius:6px;background:linear-gradient(180deg,#9c6a3c,#6e4626)}
.show-band{position:absolute;left:14px;top:157px;width:317px;height:36px;background:#e8336b;text-align:center;font-family:"Josefin Sans",sans-serif;font-weight:700;font-size:24px;color:#222;line-height:38px}
.show-sub{position:absolute;top:195px;width:100%;text-align:center;font-family:"Josefin Sans",sans-serif;font-weight:600;font-size:17px;color:#222}

/* welcome */
.welcome-small{left:0;top:1016px;width:1200px;text-align:center;font-family:"Josefin Sans",sans-serif;font-size:24px;color:var(--ink)}
.welcome-large{left:0;top:1038px;width:1200px;text-align:center;font-family:"Josefin Sans",sans-serif;font-size:36px;color:var(--ink)}
.welcome-large b{font-weight:700}
.welcome-body{left:80px;top:1101px;width:1040px;text-align:center;font-size:14px;line-height:23px;color:#555}
.btn-read{left:542px;top:1226px;width:120px;height:36px;border-radius:18px;background:var(--blue);color:#fff;font-size:13px;font-weight:600;text-align:center;line-height:36px}

/* reviews */
.reviews-band{left:0;top:1346px;width:1200px;height:220px;background:var(--gold)}
.reviews-tab{left:427px;top:1326px;width:346px;height:44px;background:var(--gold);border-radius:24px 24px 0 0;text-align:center;color:#fff;font-family:"Josefin Sans",sans-serif;font-weight:600;font-size:22px;line-height:50px}
.review{top:1444px;width:332px;height:236px;background:var(--paper);box-shadow:0 2px 5px rgba(0,0,0,.12)}
.review .q-open{position:absolute;left:14px;top:-6px;font-family:"Cormorant Garamond",serif;font-size:72px;color:#d8d8d8}
.review .q-close{position:absolute;right:14px;top:148px;font-family:"Cormorant Garamond",serif;font-size:72px;color:#d8d8d8}
.review .text{position:absolute;left:24px;top:26px;width:284px;text-align:center;font-family:"Josefin Sans",sans-serif;font-size:15px;line-height:28px;color:#555}
.review .foot{position:absolute;left:0;bottom:0;width:100%;height:68px;border-top:1px solid #e4e4e4;background:#f7f7f7}
.review .name{position:absolute;left:28px;top:12px;font-family:"Josefin Sans",sans-serif;font-weight:600;font-size:19px;color:#222}
.review .role{position:absolute;left:28px;top:36px;font-family:"Josefin Sans",sans-serif;font-size:13px;color:var(--muted)}
.review .stars{position:absolute;left:222px;top:26px;font-size:16px;letter-spacing:1px;color:var(--star)}
.review .stars .off{color:#ccc}
.avatar{top:1400px;width:68px;height:68px;border-radius:50%;background:linear-gradient(160deg,#c9b7a4,#7a6a5c);border:3px solid #fff;box-shadow:0 1px 3px rgba(0,0,0,.2)}
.divider{left:73px;top:1707px;width:1052px;height:1px;background:#cfcfcf}

/* expertise / donate */
.card{background:var(--paper);box-shadow:0 1px 4px rgba(0,0,0,.08)}
.expertise{left:73px;top:1773px;width:692px;height:210px;text-align:center;font-family:"Josefin Sans",sans-serif;color:var(--muted)}
.expertise h2{margin-top:48px;font-weight:400;font-size:25px;color:var(--blue);display:flex;justify-content:center;align-items:center;gap:12px}
.expertise h2 .rule{width:54px;height:2px;background:#bbb}
.expertise p{font-size:16px;line-height:28px}
.expertise .sub{font-size:19px;color:#555}
.dot{color:#bbb;margin:0 6px}
.donate{left:73px;top:2014px;width:692px;height:212px;text-align:center}
.donate p{margin-top:50px;font-family:"Josefin Sans",sans-serif;font-size:21px;color:#333}
.badge{top:2094px;height:70px;border-radius:8px}

/* inquiry */
.inquiry{left:793px;top:1773px;width:332px;height:453px}
.inquiry-ribbon{left:793px;top:1773px;width:332px;height:116px}
.inq-top{left:793px;top:1782px;width:332px;text-align:center;color:#fff;font-weight:600;font-size:16px}
.inq-pill{left:812px;top:1810px;width:294px;height:36px;border-radius:18px;background:var(--blue);color:#fff;text-align:center;font-family:"Josefin Sans",sans-serif;font-size:27px;line-height:40px}
.inq-note{left:813px;top:1850px;width:292px;text-align:center;color:#fff;font-size:13px;line-height:18px}
.field{left:812px;width:294px;height:38px;border-radius:4px;background:var(--field);color:#777;font-size:13px;padding:10px 10px}
.submit{left:812px;top:2165px;width:294px;height:42px;border-radius:4px;background:var(--blue-soft);color:#fff;font-weight:700;font-size:15px;text-align:center;line-height:42px}

/* footer */
.footer-wave{left:0;top:2255px;width:1200px;height:360px}
.f-col{top:2366px;color:#fff;font-size:13px;line-height:24px}
.f-col h3{font-size:13px;font-weight:700;text-transform:uppercase;margin-bottom:16px;padding-bottom:6px;border-bottom:1px solid rgba(255,255,255,.15)}
.f-row{display:flex;gap:12px;align-items:flex-start;margin-bottom:16px}
.map{left:613px;top:2426px;width:243px;height:159px;background:linear-gradient(135deg,#ece7db,#d8dccf 50%,#e8e2d2)}
.bottom-bar{left:0;top:2614px;width:1200px;height:53px;background:var(--gold);color:#fff;font-size:13px}
.copy{position:absolute;left:73px;top:17px}
.bar-social{position:absolute;right:73px;top:13px;display:flex;gap:18px;align-items:center}
.bar-social span{display:flex;gap:7px;align-items:center}
.ring{width:26px;height:26px;border-radius:50%;border:2px solid #fff}
</style>
</head>
<body>
<div class="page">

  <div class="abs hero-photo" role="img" aria-label="Photo of a woman on a wooden pier over the sea holding a flowing red scarf at sunset"></div>
  <div class="abs beach-photo" role="img" aria-label="Photo of soft surf rolling over a sandy beach"></div>

  <div class="abs hero-title small">Lorem Ipsum Dolor Sit Amet</div>
  <div class="abs hero-title large">Consectetur Adipiscing Elit</div>
  <svg class="abs slide-arrow" style="left:28px" viewBox="0 0 36 36"><circle cx="18" cy="18" r="15" fill="none" stroke="#fff" stroke-width="2" opacity=".8"/><path d="M21 11l-7 7 7 7" fill="none" stroke="#fff" stroke-width="2.5" opacity=".8"/></svg>
  <svg class="abs slide-arrow" style="left:1136px" viewBox="0 0 36 36"><circle cx="18" cy="18" r="15" fill="none" stroke="#fff" stroke-width="2" opacity=".8"/><path d="M15 11l7 7-7 7" fill="none" stroke="#fff" stroke-width="2.5" opacity=".8"/></svg>

  <header class="abs header">
    <div class="brand"><span class="pre">Dr.</span> Maren K. Kalvoric</div>
    <div class="social"><span>Friendora</span><span>Chirplet</span><span>Rivo</span></div>
    <nav class="nav"><span>HOME</span><span>SESSIONS</span><span>RESOURCES</span><span>BIO</span><span>CONTACT</span></nav>
  </header>
  <div class="abs contact-tab">
    <div class="phone">(949) 555 0142</div>
    <div class="mail">mk@drkalvoric.com</div>
  </div>
  <svg class="abs address-ribbon" viewBox="0 0 257 76" preserveAspectRatio="none"><polygon points="0,0 257,0 257,62 128,76 0,62" fill="var(--gold)"/></svg>
  <div class="abs address-text">418 Harbor Lane #210<br>Coastview, CA 92600</div>

  <div class="abs tile-panel"></div>
  <div class="abs tile tile-portrait" role="img" aria-label="Portrait photo of the psychologist">
    <div class="tile-label" style="left:16px">DR. MAREN K</div>
  </div>
  <div class="abs tile tile-video" role="img" aria-label="Video still of a counseling session">
    <svg class="play-icon" width="72" height="72" viewBox="0 0 72 72"><circle cx="36" cy="36" r="32" fill="none" stroke="#fff" stroke-width="5"/><polygon points="28,20 52,36 28,52" fill="#fff"/></svg>
    <div class="tile-label" style="width:100%;text-align:center">WATCH OUR VIDEO</div>
  </div>
  <div class="abs tile tile-radio">
    <div class="radio-head">RADIO SPOTS</div>
    <div class="radio-set" role="img" aria-label="Illustration of a vintage radio"></div>
    <div class="show-band">SILVER CEDAR TUNES</div>
    <div class="show-sub">With Nora and Elise</div>
  </div>

  <div class="abs welcome-small">Welcome to</div>
  <div class="abs welcome-large">DR. <b>MAREN K. KALVORIC</b></div>
  <p class="abs welcome-body">I'm so glad you are here. Choosing to see a professional for issues in your life can be difficult but also possibly life changing. Many postpone seeking help because they believe doing so acknowledges failure on their part. Really? We seek the help of experts all the time (contractors, mechanics, chefs, etc...) and what is more important than your life? Consulting with a neutral party to act in your best interest can be time well spent. So if you are willing to take the time to invest in counseling, make sure that it is with someone that is worth your time.</p>
  <div class="abs btn-read">READ MORE</div>

  <div class="abs reviews-band"></div>
  <div class="abs reviews-tab">REVIEWS FROM PATIENTS</div>

  <article class="abs review" style="left:73px">
    <div class="q-open">“</div>
    <p class="text">Lorem ipsum dolor sit amet, consectetur adipiscing elit, sed do eiusmod tempor incididunt ut labore et dolore magna aliqua. Ut enim ad minim veniam, quis nostrud.</p>
    <div class="q-close">”</div>
    <div class="foot"><div class="name">John Doe</div><div class="role">Lorem Ipsum</div><div class="stars">★★★★<span class="off">★</span></div></div>
  </article>
  <article class="abs review" style="left:434px">
    <div class="q-open">“</div>
    <p class="text">Lorem ipsum dolor sit amet, consectetur adipiscing elit, sed do eiusmod tempor incididunt ut labore et dolore magna aliqua. Ut enim ad minim veniam, quis nostrud.</p>
    <div class="q-close">”</div>
    <div class="foot"><div class="name">John Doe</div><div class="role">Lorem Ipsum</div><div class="stars">★★★★<span class="off">★</span></div></div>
  </article>
  <article class="abs review" style="left:793px">
    <div class="q-open">“</div>
    <p class="text">Lorem ipsum dolor sit amet, consectetur adipiscing elit, sed do eiusmod tempor incididunt ut labore et dolore magna aliqua. Ut enim ad minim veniam, quis nostrud.</p>
    <div class="q-close">”</div>
    <div class="foot"><div class="name">John Doe</div><div class="role">Lorem Ipsum</div><div class="stars">★★★★<span class="off">★</span></div></div>
  </article>
  <div class="abs avatar" style="left:205px" role="img" aria-label="Patient photo"></div>
  <div class="abs avatar" style="left:566px" role="img" aria-label="Patient photo"></div>
  <div class="abs avatar" style="left:925px" role="img" aria-label="Patient photo"></div>

  <div class="abs divider"></div>
  <svg class="abs" style="left:560px;top:1694px" width="80" height="26" viewBox="0 0 80 26">
    <rect x="0" y="0" width="80" height="26" fill="var(--page)"/>
    <circle cx="14" cy="13" r="10" fill="none" stroke="var(--gold)" stroke-width="2"/><path d="M16 8l-5 5 5 5" fill="none" stroke="var(--gold)" stroke-width="2"/>
    <line x1="35" y1="13" x2="45" y2="13" stroke="#bbb" stroke-width="1.5"/>
    <circle cx="66" cy="13" r="10" fill="none" stroke="var(--gold)" stroke-width="2"/><path d="M64 8l5 5-5 5" fill="none" stroke="var(--gold)" stroke-width="2"/>
  </svg>

  <section class="abs card expertise">
    <h2><span class="rule"></span>EXPERTISE<span class="rule"></span></h2>
    <p>Dating<span class="dot">•</span>Marriage<span class="dot">•</span>Parenting &amp; Professional</p>
    <p class="sub">RELATIONSHIPS</p>
    <p>Depression &amp; Anxiety Issues<span class="dot">•</span>Personality Disorders<span class="dot">•</span>Life Management</p>
  </section>

  <section class="abs card donate">
    <p>A portion of all revenue is donated to</p>
  </section>
  <div class="abs badge" style="left:222px;width:176px;background:#dfe6f1" role="img" aria-label="Kindred Advocates partner badge"></div>
  <div class="abs badge" style="left:448px;width:190px;background:#e7ebd6" role="img" aria-label="Willow Haven partner badge"></div>

  <section class="abs card inquiry"></section>
  <svg class="abs inquiry-ribbon" viewBox="0 0 332 116" preserveAspectRatio="none"><polygon points="0,0 332,0 332,100 166,116 0,100" fill="var(--gold)"/></svg>
  <div class="abs inq-top">CONTACT US TODAY FOR YOUR</div>
  <div class="abs inq-pill">QUICK INQUIRY</div>
  <div class="abs inq-note">Fill out the form below and we'll be in touch<br>within 24 hours!</div>
  <div class="abs field" style="top:1922px">Name</div>
  <div class="abs field" style="top:1971px">Email</div>
  <div class="abs field" style="top:2020px">Phone</div>
  <div class="abs field" style="top:2069px;height:84px">How Can we help you?</div>
  <div class="abs submit">SUBMIT</div>

  <svg class="abs footer-wave" viewBox="0 0 1200 360" preserveAspectRatio="none"><path d="M0 30 Q300 0 600 22 T1200 14 V360 H0 Z" fill="var(--navy)"/></svg>

  <div class="abs f-col" style="left:73px;width:250px">
    <h3 style="border:0;margin-bottom:0;padding-bottom:0">Clinical Psychologist</h3>
    <div style="margin-bottom:14px">California # PSY20481</div>
    <div>Doctoral Degree in Clinical Psychology<br>Masters Degree in Counseling<br>Psychology Doctoral Internship, CSU<br>Medical Center Masters Internship,<br>Brookline Clinic</div>
  </div>
  <div class="abs f-col" style="left:345px;width:240px">
    <h3>Contact Information</h3>
    <div class="f-row"><svg width="20" height="22" viewBox="0 0 20 22"><path d="M10 1a7 7 0 0 0-7 7c0 5 7 13 7 13s7-8 7-13a7 7 0 0 0-7-7z" fill="#fff"/><circle cx="10" cy="8" r="2.6" fill="var(--navy)"/></svg><div style="line-height:20px">418 Harbor Lane, Suite 210<br>Coastview, CA 92600</div></div>
    <div class="f-row"><svg width="20" height="20" viewBox="0 0 20 20"><path d="M4 1l4 4-2 3c1 3 3 5 6 6l3-2 4 4-3 3C9 19 1 11 1 4z" fill="#fff"/></svg><div style="font-size:17px">(949) 555 0142</div></div>
    <div class="f-row"><svg width="22" height="16" viewBox="0 0 22 16"><rect x="1" y="1" width="20" height="14" fill="#fff"/><path d="M1 1l10 8 10-8" fill="none" stroke="var(--navy)" stroke-width="1.6"/></svg><div>mk@drkalvoric.com</div></div>
  </div>
  <div class="abs f-col" style="left:613px;width:243px"><h3>Find Us On Map</h3></div>
  <div class="abs map" role="img" aria-label="Street map showing the office location"></div>
  <div class="abs f-col" style="left:883px;width:242px">
    <h3>Quick Links</h3>
    <div>Home<br>Sessions<br>Resources<br>Bio<br>Contact</div>
  </div>

  <footer class="abs bottom-bar">
    <div class="copy">©2016 Dr. Maren K. Kalvoric. All Rights Reserved.</div>
    <div class="bar-social">
      <span><i class="ring"></i>Rivo</span>
      <span><i class="ring"></i>Friendora</span>
      <span><i class="ring"></i>Chirplet</span>
    </div>
  </footer>

</div>
</body>
</html>
```